Velmora Freightway Solutions Business cards

Would like a very unique design catchy but professional for business cards. Please use log provided.Marlon WellsCeo and Founder TransCon Logistix Solutions1-888-913-3225mwells@tlsolutionsus.comwww.tlsolutionsus.com

```html
<!DOCTYPE html>
<html lang="en">
<head>
<meta charset="utf-8">
<title>Velmora Freightway Solutions — Business Cards</title>
<link href="https://fonts.googleapis.com/css2?family=Open+Sans:wght@400;600&display=swap" rel="stylesheet">
<style>
  :root {
    --backdrop: #7a5e40;
    --card-white: #ffffff;
    --brand-red: #ed1f27;
    --brand-blue: #0f72b8;
    --ink: #3a3a3a;
    --rule: #4a4a4a;
  }
  * { margin: 0; padding: 0; box-sizing: border-box; }
  html, body { width: 900px; height: 1200px; overflow: hidden; }
  body {
    background: var(--backdrop);
    font-family: "Open Sans", Arial, sans-serif;
    position: relative;
  }
  .card {
    position: absolute;
    left: 87px;
    width: 734px;
    height: 428px;
    border-radius: 24px;
    box-shadow: 0 4px 8px rgba(0,0,0,0.35);
  }
  .card--front { top: 137px; background: var(--card-white); }
  .card--back { top: 634px; background: var(--brand-red); }

  .brand {
    position: absolute;
    left: 0; right: 0;
    display: flex;
    justify-content: center;
    align-items: center;
    gap: 14px;
    font-weight: 600;
    white-space: nowrap;
  }
  .brand__square { display: block; }
  .card--front .brand { top: 120px; font-size: 30px; color: var(--brand-blue); }
  .card--front .brand__square { width: 22px; height: 22px; background: var(--brand-blue); }
  .card--back .brand { top: 190px; font-size: 40px; color: #fff; }
  .card--back .brand__square { width: 30px; height: 30px; background: #fff; }

  .person {
    position: absolute;
    right: 394px;
    top: 288px;
    text-align: right;
    color: var(--ink);
    font-size: 17px;
    line-height: 23px;
  }
  .person__name { color: var(--brand-blue); font-size: 24px; font-weight: 600; line-height: 34px; }

  .divider {
    position: absolute;
    left: 362px;
    top: 288px;
    width: 2px;
    height: 86px;
    background: linear-gradient(to bottom, transparent, var(--rule) 20%, var(--rule) 80%, transparent);
  }

  .contacts {
    position: absolute;
    left: 384px;
    top: 296px;
    list-style: none;
    color: var(--ink);
    font-size: 17px;
    line-height: 23px;
  }
  .contacts li { display: flex; align-items: center; gap: 10px; }
  .contacts svg { width: 13px; height: 13px; flex: none; }
  .contacts .accent { color: var(--brand-blue); }

  .back-url {
    position: absolute;
    left: 0; right: 0;
    top: 366px;
    text-align: center;
    color: #fff;
    font-size: 17px;
    letter-spacing: 1.2px;
  }
</style>
</head>
<body>
  <section class="card card--front">
    <div class="brand"><span class="brand__square"></span>Velmora Freightway Solutions</div>

    <div class="person">
      <div class="person__name">Dorian Pike</div>
      <div class="person__title">Ceo and Founder</div>
      <div class="person__company">Velmora Freightway Solutions</div>
    </div>

    <div class="divider"></div>

    <ul class="contacts">
      <li>
        <svg viewBox="0 0 16 16" aria-hidden="true"><path fill="#ed1f27" d="M3.5 1.5l2.5 0 1 3.5-1.6 1.2a9 9 0 0 0 4.4 4.4L11 9l3.5 1v2.5c0 1-1 2-2 2C6.5 14.5 1.5 9.5 1.5 3.5c0-1 1-2 2-2z"/></svg>
        <span>1-888-470-6158</span>
      </li>
      <li>
        <svg viewBox="0 0 16 16" aria-hidden="true"><rect x="1" y="3" width="14" height="10" rx="1" fill="#ed1f27"/><path d="M1.5 4l6.5 5 6.5-5" stroke="#fff" stroke-width="1.3" fill="none"/></svg>
        <span>dpike@<span class="accent">vfwayroutes</span>.com</span>
      </li>
      <li>
        <svg viewBox="0 0 16 16" aria-hidden="true"><g fill="none" stroke="#ed1f27" stroke-width="1.4"><circle cx="8" cy="8" r="6.3"/><ellipse cx="8" cy="8" rx="2.8" ry="6.3"/><path d="M1.7 8h12.6M2.8 4.8h10.4M2.8 11.2h10.4"/></g></svg>
        <span>www.<span class="accent">vfwayroutes</span>.com</span>
      </li>
    </ul>
  </section>

  <section class="card card--back">
    <div class="brand"><span class="brand__square"></span>Velmora Freightway Solutions</div>
    <div class="back-url">www.vfwayroutes.com</div>
  </section>
</body>
</html>
```